Maris Dovey Studio Business Cards

Hi - using the information and logo provided I require a two sided business card designed with the following information. The business card is a 'mini card' 3.5" x 1.25".

Front of card should be the logo attached but inverted (so the background is the peach colour and the logo white).

Back should have these details. If we can't fit the Pictogrum and Friendwall part can we just put the little logos.

Tessa Varnold

Art and Design Consultant
Dealer - Curator - Events - Styling - Creative Sourcing

P: 0438 217 604
E: tessa@marisdoveystudio.example
W: www.marisdoveystudio.example
I (pictogram image please): marisdoveystudio F (Friendwall image please): MarisDoveyAdviser

Target Market(s)

Galleries, artists, art buyers, interior design clients, event managers, creative types

Industry/Entity Type

Business

```html
<!DOCTYPE html>
<html lang="en">
<head>
<meta charset="utf-8">
<title>Maris Dovey Studio – Mini Business Card</title>
<link href="https://fonts.googleapis.com/css2?family=Tinos:wght@400&display=swap" rel="stylesheet">
<style>
  :root {
    --backdrop: #5e4f47;
    --card-black: #141414;
    --card-white: #ffffff;
    --peach: #f3b79b;
    --ink: #1e1e1e;
    --slate: #6b6b6b;
    --rule: #2a2a2a;
  }
  * { margin: 0; padding: 0; box-sizing: border-box; }
  html, body {
    width: 1200px; height: 960px; overflow: hidden;
    background: var(--backdrop);
    font-family: "Tinos", "Times New Roman", serif;
  }
  .canvas { position: relative; width: 1200px; height: 960px; }

  .card {
    position: absolute;
    width: 713px; height: 254px;
    overflow: hidden;
    box-shadow: 0 18px 24px -14px rgba(0,0,0,.45);
  }

  /* Front */
  .card-front { left: 118px; top: 113px; background: var(--card-black); }
  .brand-panel {
    position: absolute; left: 34px; top: 0;
    width: 257px; height: 200px;
    background: var(--card-white);
    border-radius: 0 0 16px 16px;
    display: flex; flex-direction: column; align-items: center;
    overflow: hidden;
  }
  .brand-panel .brand-dot {
    width: 94px; height: 94px; border-radius: 50%;
    background: var(--peach);
    margin-top: 18px;
  }
  .brand-panel .brand-name {
    margin-top: 22px;
    font-size: 16px; letter-spacing: 2px;
    color: var(--slate);
    text-transform: uppercase;
    white-space: nowrap;
  }
  .rule-top {
    position: absolute; left: 311px; right: 0; top: 23px; height: 6px;
    background: var(--peach);
  }
  .rule-bottom {
    position: absolute; left: 0; right: 0; top: 226px; height: 6px;
    background: var(--peach);
  }
  .person-name {
    position: absolute; left: 311px; top: 38px;
    font-size: 31px; font-weight: 400; color: var(--peach); white-space: nowrap;
  }
  .person-role {
    position: absolute; left: 311px; top: 76px;
    font-size: 18px; color: var(--peach); white-space: nowrap;
  }
  .services {
    position: absolute; left: 311px; top: 107px;
    font-size: 15px; color: var(--peach); white-space: nowrap;
  }

  /* Back */
  .card-back { left: 374px; top: 514px; background: var(--card-white); }
  .back-brand {
    position: absolute; left: 35px; top: 22px; width: 160px;
    display: flex; flex-direction: column; align-items: center;
  }
  .back-brand .brand-dot {
    width: 100px; height: 100px; border-radius: 50%;
    background: var(--peach);
  }
  .back-brand .brand-name {
    margin-top: 10px;
    font-size: 11px; letter-spacing: 1.5px;
    color: var(--slate); text-transform: uppercase; white-space: nowrap;
  }
  .contact-list {
    position: absolute; left: 229px; top: 30px;
    list-style: none;
    font-size: 23px; line-height: 39px; color: var(--ink);
    white-space: nowrap;
  }
  .social-bar {
    position: absolute; left: 31px; right: 31px; top: 176px; height: 53px;
    border-top: 3px solid var(--rule);
    border-bottom: 3px solid var(--rule);
    font-size: 19px; color: var(--ink);
  }
  .social-item { position: absolute; top: 12px; white-space: nowrap; }
  .social-network { margin-right: 10px; }
  .social-item.friendwall { left: 6px; }
  .social-item.pictogrum { left: 373px; }
</style>
</head>
<body>
<main class="canvas">

  <section class="card card-front" aria-label="Card front">
    <div class="brand-panel">
      <span class="brand-dot"></span>
      <span class="brand-name">Maris Dovey Studio</span>
    </div>
    <div class="rule-top"></div>
    <h1 class="person-name">Tessa Varnold</h1>
    <p class="person-role">(Art and Design Consultant)</p>
    <p class="services">Dealer | Curator | Events | Styling | Creative Sourcing</p>
    <div class="rule-bottom"></div>
  </section>

  <section class="card card-back" aria-label="Card back">
    <div class="back-brand">
      <span class="brand-dot"></span>
      <span class="brand-name">Maris Dovey Studio</span>
    </div>
    <ul class="contact-list">
      <li>T: 0438 217 604</li>
      <li>E: tessa@marisdoveystudio.example</li>
      <li>W: www.marisdoveystudio.example</li>
    </ul>
    <div class="social-bar">
      <span class="social-item friendwall"><span class="social-network">Friendwall</span>marisdoveystudio F</span>
      <span class="social-item pictogrum"><span class="social-network">Pictogrum</span>MarisDoveyAdviser</span>
    </div>
  </section>

</main>
</body>
</html>
```